Post Disaster Temporary Housing Literature Review poster

Wanting a poster design for two Emergency Management conferences we have coming up. The information to be included in the poster is capturing the purpose, findings and recommendations from a post disaster temporary housing literature review looking at “What should government consider in order to improve planning and decision making for accommodation needs after a disaster, and to support people’s transition to stable housing?”
I’d like to enhance the visual appeal through including relevant images or graphic. I am also open to reducing the text if needed.
The government group I work with focuses on the social and human side of disaster recovery so keen for any images to reflect the human aspect and not focus solely on disasters or housing.
Government and NGO's

```html
<!DOCTYPE html>
<html lang="en">
<head>
<meta charset="utf-8">
<title>Post Disaster Temporary Housing Literature Review</title>
<link href="https://fonts.googleapis.com/css2?family=Poppins:wght@400;500;600;700;800&family=Teko:wght@500;600&display=swap" rel="stylesheet">
<style>
:root{
  --teal-dark:#10506b;
  --blue-bright:#1b8fc6;
  --blue-light:#5cbbd9;
  --panel:#7cc4de;
  --ink:#1a2830;
  --white:#ffffff;
  --sub:#cfeefa;
}
*{margin:0;padding:0;box-sizing:border-box}
html,body{width:730px;height:1200px;overflow:hidden;background:#ffffff}
body{font-family:'Poppins',sans-serif;color:var(--ink)}
.poster{position:relative;width:730px;height:1200px;overflow:hidden;background:var(--white)}

/* Header */
.brand{position:absolute;left:52px;top:42px;display:flex;align-items:center;gap:22px}
.brand-mark{width:88px;height:88px;border-radius:50%;border:4px solid var(--blue-light);flex:none}
.brand-name{font-weight:400;font-size:15.5px;line-height:18px;color:var(--ink)}
.brand-name .country{display:block;font-size:11px;letter-spacing:1.8px;margin-top:3px}
.hero-art{position:absolute;left:388px;top:10px;width:320px;height:250px;border-radius:14px;
  background:radial-gradient(circle at 80% 22%,#f4f4f4 0%,#e2e5ea 28%,rgba(255,255,255,0) 52%),
  linear-gradient(160deg,#ffffff 0%,#dfe6f4 38%,#4b6ed0 60%,#8fb45a 80%,#5d4a5a 100%)}
.title{position:absolute;left:48px;top:148px;width:330px}
.title-pre{font-weight:800;font-size:26px;color:var(--blue-light);line-height:27px}
.title-main{height:38px}
.title-main span{display:inline-block;font-family:'Teko',sans-serif;font-weight:600;font-size:43px;line-height:32px;color:var(--blue-bright);transform:scaleY(1.2);transform-origin:left top;letter-spacing:-.3px}
.title-sub{font-weight:800;font-size:26px;line-height:26px;color:#111;letter-spacing:1.8px}
.badge{display:inline-flex;margin-top:6px;border:1.5px solid var(--blue-bright);border-radius:4px;overflow:hidden}
.badge-a{font-weight:700;font-size:13px;color:var(--blue-light);padding:0 5px;line-height:16px}
.badge-b{font-weight:500;font-size:13px;color:#fff;background:var(--blue-bright);padding:0 5px;line-height:16px;letter-spacing:5px}
.avail{position:absolute;left:48px;top:261px;font-size:8.5px;letter-spacing:2.6px;font-weight:500}
.url{position:absolute;left:48px;top:275px;font-size:9.5px;font-weight:500}

/* Purpose */
.purpose{position:absolute;left:0;top:311px;width:730px;height:126px;background:var(--teal-dark);color:#fff}
.purpose-left{position:absolute;left:48px;top:9px;width:274px}
.purpose-right{position:absolute;left:384px;top:8px;width:322px}
.purpose-divider{position:absolute;left:356px;top:22px;width:1px;height:92px;background:rgba(255,255,255,.35)}
.block-title{display:flex;align-items:center;gap:7px;font-weight:700;font-size:20px;line-height:22px;color:var(--blue-light)}
.icon-ring{width:19px;height:19px;border-radius:50%;border:2.5px solid #fff;position:relative;flex:none}
.icon-ring::after{content:"";position:absolute;inset:3px;border-radius:50%;background:#fff}
.purpose p{font-size:8px;line-height:9.2px}
.purpose-left p{margin-top:4px}
.question-lead{font-weight:600;font-size:8.6px;line-height:12px;color:var(--sub)}
.question{display:flex;gap:9px;margin-top:3px}
.qmark{font-weight:300;font-size:32px;line-height:32px;color:rgba(255,255,255,.7);width:18px;flex:none}
.purpose-right .note{margin-top:5px}

/* Recommendations */
.recs{position:absolute;left:46px;top:455px;width:272px}
.sec-head{display:flex;align-items:center;gap:6px;font-weight:700;font-size:20px;line-height:24px;color:var(--teal-dark)}
.sec-icon{width:24px;height:24px;border-radius:50%;background:var(--blue-bright);border:2px solid #bfe3f3;flex:none}
.rec{margin-top:7px}
.rec:first-of-type{margin-top:4px}
.rec h3{display:flex;align-items:center;gap:5px;font-weight:600;font-size:11.5px;color:var(--blue-bright);line-height:14px}
.rec-icon{width:9px;height:10px;border:1.2px solid var(--blue-light);border-radius:1.5px;flex:none}
.rec p{font-size:8px;line-height:9.2px;margin-top:2px}
.mini-list{display:grid;grid-template-columns:134px 134px;gap:6px 4px;margin-top:5px;list-style:none}
.mini-list li{font-size:6.8px;line-height:7.8px;padding-left:8px;position:relative}
.mini-list li::before{content:"";position:absolute;left:0;top:1px;width:5px;height:5px;border-radius:50%;background:var(--blue-bright)}

/* Findings */
.findings{position:absolute;left:331px;top:437px;width:371px;height:656px;background:var(--panel);border-radius:0 0 18px 18px;padding:10px 19px 0 24px}
.find{padding:18px 0 10px;border-bottom:1px dashed rgba(255,255,255,.85)}
.find:first-of-type{padding-top:10px}
.find:last-child{border-bottom:none}
.find h3{font-weight:600;font-size:14px;line-height:16px;color:#fff;margin-bottom:12px}
.find p{font-size:7.9px;line-height:9px}
.find p + p{margin-top:5px}
.find .lead{font-weight:700}
.cats{display:grid;grid-template-columns:127px 110px 1fr;gap:8px 0;margin-top:9px;list-style:none}
.cats li{font-size:7.6px;line-height:9px;padding-left:9px;padding-right:6px;position:relative}
.cats li::before{content:"";position:absolute;left:0;top:2px;width:5px;height:5px;border-radius:50%;border:1.2px solid #fff}

/* Next steps */
.next{position:absolute;left:0;top:1102px;width:314px;height:98px;background:var(--teal-dark);border-radius:0 10px 0 0;padding:10px 16px 0 48px;color:#fff}
.next .block-title{font-size:18px}
.next .icon-ring{width:20px;height:20px;border-width:2px}
.next .icon-ring::after{inset:4px;background:transparent;border:1.5px solid #fff;border-radius:2px}
.next p{font-size:7.6px;line-height:9px;margin-top:8px}

/* Contact */
.contact{position:absolute;left:338px;top:1104px;width:392px;height:74px}
.contact-head{position:absolute;left:0;top:0;font-weight:700;font-size:15px;line-height:15.5px;color:var(--teal-dark)}
.contact-list{position:absolute;left:130px;top:1px;list-style:none}
.contact-list li{font-size:9.4px;font-weight:500;line-height:16px;padding-left:10px;position:relative;white-space:nowrap}
.contact-list li::before{content:"";position:absolute;left:0;top:5.5px;width:5px;height:5px;border-radius:50%;background:var(--blue-bright)}
.email{position:absolute;left:0;top:56px;width:392px;height:15px;background:var(--teal-dark);border-radius:7px 0 0 7px;color:#fff;font-size:8.6px;font-weight:600;letter-spacing:1.6px;line-height:15px;padding-left:18px;white-space:nowrap}
.email::before{content:"";position:absolute;left:5px;top:4px;width:7px;height:7px;border-radius:50%;background:var(--blue-light)}
</style>
</head>
<body>
<main class="poster">

  <header>
    <div class="brand">
      <span class="brand-mark"></span>
      <div class="brand-name">Social Renewal<br>Advisory Group<span class="country">AUSTRALIA</span></div>
    </div>
    <div class="hero-art" role="img" aria-label="Illustration of a house and car on a lawn being struck by a swirling storm"></div>
    <div class="title">
      <div class="title-pre">POST DISASTER</div>
      <div class="title-main"><span>TEMPORARY HOUSING</span></div>
      <div class="title-sub">LITERATURE REVIEW</div>
      <div class="badge"><span class="badge-a">SUMMARY REPORT</span><span class="badge-b">JANUARY 2024</span></div>
    </div>
    <div class="avail">THE FULL REPORT IS AVAILABLE AT</div>
    <div class="url">https://library.recoveryhub.example/resources/social-renewal-advisory-group</div>
  </header>

  <section class="purpose">
    <div class="purpose-left">
      <h2 class="block-title"><span class="icon-ring"></span>PURPOSE</h2>
      <p>There are currently significant challenges in supporting people with timely and equitable access to emergency and temporary accommodation and assisting them on a path to stable housing in the aftermath of a disaster. This report seeks to support agencies and decision makers to formulate and implement appropriate approaches to post-disaster housing, factoring in the scale of a disaster and varying community cohorts.</p>
    </div>
    <span class="purpose-divider"></span>
    <div class="purpose-right">
      <div class="question-lead">The central research question underpinning this report is:</div>
      <div class="question">
        <span class="qmark">?</span>
        <p>What should government consider in order to improve planning and decision making for accommodation needs after a disaster, and to support people’s transition to stable housing?</p>
      </div>
      <p class="note">The full report was commissioned by the Social Renewal Advisory Group (SRAG) and undertaken by Ruth Aldane and Peter Calloway through the Southern Coast Institute of Technology (SCIT). The findings and recommendations may be utilised by stakeholders.</p>
    </div>
  </section>

  <section class="recs">
    <h2 class="sec-head"><span class="sec-icon"></span>RECOMMENDATIONS</h2>
    <div class="rec"><h3><span class="rec-icon"></span>Terminology</h3><p>Develop a standard set of terminology to describe the phases and types of accommodation displaced people may access on the path to stable housing and to be adopted by State and Territory recovery agencies. The terms recommended for consideration are: Emergency and Short-Term Accommodation, Temporary Housing and Stable Housing.</p></div>
    <div class="rec"><h3><span class="rec-icon"></span>Principles</h3><p>Adopt common principles of leading practice in post-disaster housing recovery including community connection, wellbeing, liveability, viability, and sustainability, for deciding accommodation and support options for people.</p></div>
    <div class="rec"><h3><span class="rec-icon"></span>National Principles</h3><p>The Commonwealth and State/Territory governments should extend the agreed principles of disaster recovery to include principles of resilient recovery.</p></div>
    <div class="rec"><h3><span class="rec-icon"></span>Guidelines</h3><p>Develop resources and guidelines to support planning and operational response for post disaster temporary housing.</p></div>
    <div class="rec"><h3><span class="rec-icon"></span>Capacity Building</h3><p>Develop capacity building resources and programs for State/Territory agencies and local governments to support pre planning for disaster temporary housing.</p></div>
    <div class="rec"><h3><span class="rec-icon"></span>Funding</h3><p>Recognise different cost implications of temporary housing programs including indirect costs. Develop funding streams to address the priority needs.</p></div>
    <div class="rec"><h3><span class="rec-icon"></span>Further Research</h3><p>Undertake research into post disaster temporary housing topics such as:</p>
      <ul class="mini-list">
        <li>Improving housing resilience through land-use planning and building codes.</li>
        <li>Utilisation of innovative construction technologies, materials and methods.</li>
        <li>Learnings from previous disasters on suitable approaches for different communities and contexts.</li>
        <li>Utilising permanent prefabricated housing modules that transition from temporary to permanent.</li>
      </ul>
    </div>
    <div class="rec"><h3><span class="rec-icon"></span>Pilot Project</h3><p>Resource, trial and evaluate a pilot program to identify ways of achieving a two-phase approach to assisting home-owners and renter households into stable housing.</p></div>
    <div class="rec"><h3><span class="rec-icon"></span>Decision Making Framework</h3><p>Adopt the outline of a Decision-Making Framework for Disaster Housing Recovery provided in this report to provide a basis for the development of tools that can be used by multiple stakeholders in housing recovery programs and projects across different parts of Australia.</p></div>
    <div class="rec"><h3><span class="rec-icon"></span>Capturing Learnings</h3><p>Establish a national repository of evaluation reports and support processes for regular cross-case analysis.</p></div>
  </section>

  <section class="findings">
    <h2 class="sec-head"><span class="sec-icon"></span>FINDINGS</h2>
    <div class="find">
      <h3>Leading practice in<br>disaster housing recovery</h3>
      <p>The analysis of leading practices in housing recovery led to the development of a checklist of actions that could be used to identify appropriate actions by housing recovery officers and their agencies in providing and managing emergency and short-term accommodation and temporary housing. The checklist was developed from research and contains criteria for achieving eight categories of leading practice: Community Engagement &amp; Participation, Location, Safety, Health, Comfort &amp; Privacy, Cultural &amp; Special Needs, Community &amp; Connection, and Social &amp; Technical Support Services.</p>
    </div>
    <div class="find">
      <h3>Innovative approaches<br>to temporary housing</h3>
      <p>Innovative approaches to effective temporary housing practices are based upon the concept of resilient housing recovery, which has at least five dimensions: Wellbeing, Liveability, Sustainability, Community Connection, and Viability. This change of focus has two major implications:</p>
      <p>The planning of post-disaster housing and infrastructure programs needs to become one of the priority strategies in pre-disaster preparation; and</p>
      <p>Strategies are needed to establish Temporary Housing as the first step in the design and construction of on-site Stable Housing to minimise the social, economic and environmental costs incurred when displaced people spend extended periods of time in Temporary Housing.</p>
      <p>These implications are explored through strategies and tools for pre-disaster planning and the development of a two-phase model for constructing Stable Housing through a “temporary-to-permanent” construction strategy.</p>
    </div>
    <div class="find">
      <h3>A decision-making framework<br>for resilient housing recovery</h3>
      <p>The Framework seeks to integrate the steps in project management and to use the housing process as a lever for overall recovery. This involves aligning decisions at strategic and operational levels and managing the trade-offs between issues of location, tenure, housing types and procurement.</p>
      <p class="lead">There are nine such decision categories in the Framework:</p>
      <ul class="cats">
        <li>Consultation</li>
        <li>Pre-Disaster Planning for Housing Recovery</li>
        <li>Situation Analysis after a Disaster Event</li>
        <li>Recognising Cohorts of Displaced People with Different Needs and Assets</li>
        <li>Identifying and Selecting Housing Model Options</li>
        <li>Providing Agency Wrap-Around Support Services</li>
        <li>Using Housing Decisions to Promote Local Economic and Social Recovery</li>
        <li>Program Design and Delivery</li>
        <li>Monitoring and Evaluation.</li>
      </ul>
    </div>
  </section>

  <section class="next">
    <h2 class="block-title"><span class="icon-ring"></span>NEXT STEPS</h2>
    <p>The Social Renewal Advisory Group is partnering with Hazard Resilience Studies Network to analyse previous post-disaster temporary housing assistance and support mechanisms used in Australia.</p>
  </section>

  <section class="contact">
    <h2 class="contact-head">For further<br>information<br>Contact</h2>
    <ul class="contact-list">
      <li>Helen Marlowe</li>
      <li>National Consultant Disaster Recovery</li>
      <li>Social Renewal Advisory Group</li>
    </ul>
    <div class="email">helen.marlowe@recoveryoffice.example.gov</div>
  </section>

</main>
</body>
</html>
```